Exciting new website for concierge aesthetic company

Simple, elegant, fresh design for female owned concierge aesthetic company, catering to both men and women ages 30-60. We would like a home page with an exciting catch phrase, a brief description of the company and a section to fill out an appointment request that includes a section for a referral. Please also have a book appointment link in the header of all pages that will link back to booking information form on home page. Separate pages to include:
- Services = 3 different services. Each service stating the name of the service and then providing a brief description. 3 services are "Private Session" for 1 client, "Group Session" for 2-5 clients, "Party" for 6+ clients. Will provide service descriptions text later. Item at bottom of page to allow description of how to "Host a Party".
- Products = 4 different product lines. Will provide pictures of product, brief description and link to manufacturer's website.
- Stories = brief client reviews to include before and after photos
- About us = Personal picture with brief description of owner's fun, exciting and family focussed lifestyle.
*Our domain is registered with varnix and we be using varnix for website hosting.

Target Market(s)

30-60 year old men and women, but mostly women

Industry/Entity Type

beauty and aesthetics

Coding

Coded - Design and coding required

Number of Pages Required

5+ page

Font styles to use
Sans Serif
Script

Colors
59FF00
82FF00
B8FF75
E3FFCB
F4FFEA
FFC000
F8CF3A
FAE287
FDF2CF
FEFAEE
F0912C
F2A743
F7CA91
FBE8D2
FDF5EE
E54698
E96AAD
F1A4CE
F9D9EA
FCEFF6

Requirements
Must have
• coded for varnix
Should not have
• corny pictures. No needles in pictures or graphics. No medical office or medical chair in pictures.

```html
<!DOCTYPE html>
<html lang="en">
<head>
<meta charset="utf-8">
<title>Glow Muse — Concierge Aesthetics</title>
<link rel="stylesheet" href="https://fonts.googleapis.com/css2?family=Roboto:wght@400;500;700&family=Great+Vibes&display=swap">
<style>
:root{
  --pink:#e8336e;
  --pink-soft:#f9d9ea;
  --pink-faint:#fcf0f6;
  --orange:#f7781f;
  --orange-soft:#fbe8d2;
  --ink:#222;
  --body:#666;
  --dark:#1f1e21;
  --white:#fff;
  --sans:'Roboto',Arial,sans-serif;
  --script:'Great Vibes',cursive;
}
*{box-sizing:border-box;margin:0;padding:0}
html,body{width:1200px;height:4015px;overflow:hidden;background:#fff}
body{font-family:var(--sans);color:var(--ink);position:relative}
.abs{position:absolute}
.btn{position:absolute;display:flex;align-items:center;justify-content:center;gap:8px;background:linear-gradient(90deg,var(--pink),var(--orange));color:#fff;font:700 12px var(--sans);text-transform:uppercase;border-radius:3px;text-decoration:none}
.btn svg{width:12px;height:12px}
.section-title{position:absolute;left:0;width:1200px;text-align:center;font:400 58px/1 var(--script);color:var(--pink)}
.section-title::after{content:"";display:block;width:52px;height:3px;margin:18px auto 0;background:linear-gradient(90deg,var(--pink),var(--orange))}
/* header */
.site-header{position:absolute;left:0;top:0;width:1200px;height:125px;background:#fff}
.call{left:112px;top:18px;display:flex;gap:14px;align-items:center}
.call .dot{width:36px;height:36px;border-radius:50%;background:linear-gradient(135deg,var(--pink),var(--orange));display:flex;align-items:center;justify-content:center}
.call small{display:block;font:700 11px var(--sans)}
.call strong{display:block;font:500 18px var(--sans);color:var(--pink)}
.nav{top:92px;font:500 14px var(--sans);color:var(--ink)}
.nav a{position:absolute;color:var(--ink);text-decoration:none;white-space:nowrap}
.hline{top:72px;height:1px;background:#e6e6e6}
.brand-disc{left:485px;top:-60px;width:230px;height:244px;border-radius:50%;background:#fff}
.brand{left:490px;top:80px;width:220px;text-align:center;font:700 30px var(--sans);color:var(--pink)}
.brand-sub{left:490px;top:120px;width:220px;text-align:center;font:400 9px var(--sans);letter-spacing:4px;color:var(--orange)}
.brand-mark{left:581px;top:14px;width:38px;height:38px;border-radius:50%;border:2px solid var(--pink)}
.search{left:1050px;top:84px;width:36px;height:36px;border-radius:50%;background:linear-gradient(135deg,var(--pink),var(--orange));display:flex;align-items:center;justify-content:center}
/* hero */
.hero-title{left:0;top:320px;width:1200px;text-align:center;font:400 104px/1 var(--script);color:var(--pink)}
.hero-text{left:370px;top:444px;width:460px;text-align:center;font:400 14px/22px var(--sans);color:var(--body)}
/* services */
.service{width:328px;height:328px;border-radius:50%;background:linear-gradient(145deg,#f79840,#f4604a 45%,#ea3b74);display:flex;flex-direction:column;align-items:center;justify-content:center;color:#fff;top:1031px}
.service::before{content:"";position:absolute;inset:28px;border-radius:50%;border:2px solid rgba(255,255,255,.25)}
.service .ico{width:84px;height:84px;border-radius:8px;background:rgba(255,255,255,.85);margin-bottom:18px}
.service h3{font:700 26px var(--sans)}
.service h3::after{content:"";display:block;width:46px;height:2px;background:#fff;margin:12px auto 0}
/* about */
.about-text{left:665px;top:1730px;width:423px;font:400 14px/23px var(--sans);color:var(--body);text-align:justify}
.photo{border:0}
/* products */
.card{top:2420px;width:315px;height:340px;border:1px solid #e2e2e2;background:#fff;text-align:center}
.card .ph{margin:8px;height:220px;background:linear-gradient(180deg,#f3f3f3,#e9e9e9)}
.card h4{margin-top:24px;font:500 19px var(--sans)}
.card p{margin:12px 20px 0;font:400 13px/19px var(--sans);color:var(--body)}
.arrow{top:2575px}
/* stories */
.story{top:3072px;width:472px;height:392px;background:linear-gradient(110deg,#fcdcec 0 40%,#fdefe0 40%);overflow:hidden}
.story p{position:absolute;left:44px;top:42px;width:388px;font:400 13.5px/22px var(--sans);color:var(--body);text-align:justify}
.story .who{position:absolute;left:44px;top:142px;font:400 13px var(--sans);color:var(--ink)}
.story .who b{font-weight:700}
.story .q{position:absolute;right:44px;top:138px;font:900 40px/1 Georgia,serif;color:var(--pink)}
.story .lbl{position:absolute;top:190px;font:700 18px var(--sans)}
.story .face{position:absolute;top:222px;width:150px;height:170px;background:linear-gradient(180deg,#e7b8a8,#d29b8a)}
/* footer */
.foot-h{font:700 14px var(--sans);color:#fff;text-transform:uppercase}
.foot-list{list-style:none;font:400 13px var(--sans);color:#fff}
.foot-list li{height:30px;display:flex;align-items:center;gap:16px}
.foot-list li::before{content:"»";color:var(--pink);font-size:14px}
.contact li{display:flex;gap:16px;align-items:center;font:400 12.5px/16px var(--sans);color:#fff;margin-bottom:20px}
.contact .ic{flex:none;width:26px;height:26px;border-radius:50%;background:#3a393d}
.socials{left:824px;top:3876px;display:flex;gap:10px}
.socials span{width:30px;height:30px;border-radius:50%;background:#fff;display:block}
.socials span:nth-child(2){background:var(--pink)}
.copy{left:0;top:3965px;width:1200px;height:50px;background:var(--pink);color:#fff;font:400 14px/50px var(--sans);text-align:center}
</style>
</head>
<body>

<!-- HERO BACKGROUND -->
<svg class="abs" style="left:0;top:125px" width="1200" height="730" viewBox="0 0 1200 730" aria-hidden="true">
  <defs><linearGradient id="heroEdge" x1="0" x2="1"><stop offset="0" stop-color="#e8336e"/><stop offset="1" stop-color="#f7781f"/></linearGradient></defs>
  <path d="M0 0H1200V490Q600 930 0 490Z" fill="#fbeef4"/>
  <path d="M0 490Q600 930 1200 490" fill="none" stroke="url(#heroEdge)" stroke-width="4"/>
</svg>
<div class="abs" role="img" aria-label="Silhouette of a man's profile filled with a misty mountain and forest scene" style="left:0;top:230px;width:320px;height:430px;border-radius:45% 55% 10% 30%;background:linear-gradient(180deg,#f6c6da 0 40%,#c7a7cf 60%,#6b6aa5)"></div>
<div class="abs" role="img" aria-label="Silhouette of a woman's profile filled with a misty mountain and forest scene" style="left:860px;top:275px;width:340px;height:380px;border-radius:55% 45% 20% 10%;background:linear-gradient(180deg,#f6c6da 0 40%,#c7a7cf 60%,#6b6aa5)"></div>
<h1 class="abs hero-title">Glow Muse</h1>
<p class="abs hero-text">Lorem ipsum dolor sit amet, consectetur adipiscing elit, sed do eiusmod tempor incididunt ut labore et dolore magna aliqua.</p>
<a class="btn" href="#book" style="left:503px;top:513px;width:193px;height:42px">Book an appointment <svg viewBox="0 0 12 12"><rect x="1" y="2" width="10" height="9" fill="none" stroke="#fff" stroke-width="1.4"/><path d="M1 5h10M4 1v2M8 1v2" stroke="#fff" stroke-width="1.4"/></svg></a>

<!-- HEADER -->
<header class="site-header">
  <div class="abs call"><span class="dot"><svg width="16" height="16" viewBox="0 0 24 24"><path d="M6.6 10.8a15 15 0 0 0 6.6 6.6l2.2-2.2a1 1 0 0 1 1-.25 11.4 11.4 0 0 0 3.6.6 1 1 0 0 1 1 1V20a1 1 0 0 1-1 1A17 17 0 0 1 3 4a1 1 0 0 1 1-1h3.5a1 1 0 0 1 1 1c0 1.25.2 2.45.6 3.6a1 1 0 0 1-.25 1z" fill="#fff"/></svg></span><div><small>CALL US TODAY !</small><strong>+1 555 014 2290</strong></div></div>
  <div class="abs hline" style="left:112px;width:375px"></div>
  <div class="abs hline" style="left:713px;width:375px"></div>
  <nav class="abs nav" style="left:0;width:1200px">
    <a style="left:114px">Home</a><a style="left:196px">Services</a><a style="left:296px">Our Products</a>
    <a style="left:774px">About</a><a style="left:857px">Stories</a><a style="left:946px">Contact Us</a>
  </nav>
  <div class="abs brand-disc"></div>
  <div class="abs brand-mark"></div>
  <div class="abs brand">Glow Muse</div>
  <div class="abs brand-sub">CONCIERGE AESTHETICS</div>
  <a class="btn" href="#book" style="left:894px;top:12px;width:193px;height:43px">Book an appointment <svg viewBox="0 0 12 12"><rect x="1" y="2" width="10" height="9" fill="none" stroke="#fff" stroke-width="1.4"/><path d="M1 5h10M4 1v2M8 1v2" stroke="#fff" stroke-width="1.4"/></svg></a>
  <span class="abs search"><svg width="14" height="14" viewBox="0 0 14 14"><circle cx="6" cy="6" r="4.2" fill="none" stroke="#fff" stroke-width="2"/><path d="M9 9l4 4" stroke="#fff" stroke-width="2"/></svg></span>
</header>

<!-- SERVICES -->
<h2 class="section-title" style="top:912px">Our Services</h2>
<div class="abs service" style="left:88px"><span class="ico" role="img" aria-label="Private session icon"></span><h3>Private Session</h3></div>
<div class="abs service" style="left:436px"><span class="ico" role="img" aria-label="Group session icon"></span><h3>Group Session</h3></div>
<div class="abs service" style="left:782px"><span class="ico" role="img" aria-label="Party icon"></span><h3>Party</h3></div>

<!-- ABOUT -->
<svg class="abs" style="left:0;top:1430px" width="1200" height="800" viewBox="0 0 1200 800" aria-hidden="true">
  <defs><linearGradient id="aboutEdge" x1="0" x2="1"><stop offset="0" stop-color="#e8336e"/><stop offset="1" stop-color="#e8336e"/></linearGradient></defs>
  <path d="M0 80Q500 -40 1200 20V690Q700 820 0 690Z" fill="#fbeef4"/>
  <path d="M0 80Q250 20 520 5L480 25Q220 45 0 105Z" fill="#f7891f"/>
  <path d="M1200 690Q900 790 600 790Q1000 760 1200 665Z" fill="url(#aboutEdge)"/>
</svg>
<h2 class="section-title" style="top:1540px">About Us</h2>
<div class="abs photo" role="img" aria-label="Photo of a smiling man receiving a skin treatment" style="left:112px;top:1708px;width:371px;height:321px;background:linear-gradient(135deg,#c9d4e4,#8fa8c9 50%,#3f62b5)"></div>
<div class="abs photo" role="img" aria-label="Photo of a woman relaxing during a facial treatment" style="left:343px;top:1905px;width:233px;height:203px;background:linear-gradient(135deg,#f2ece8,#e5cfc0 55%,#c9a08a)"></div>
<p class="abs about-text">Lorem ipsum dolor sit amet, consectetur adipiscing elit, sed do eiusmod tempor incididunt ut labore et dolore magna aliqua. Ut enim ad minim veniam, quis nostrud exercitation ullamco laboris nisi ut aliquip ex ea commodo consequat. Duis aute irure dolor in reprehenderit in voluptate velit esse cillum dolore eu fugiat nulla pariatur. Excepteur sint occaecat cupidatat non proident, sunt in culpa qui officia deserunt mollit anim id est laborum Lorem ipsum dolor sit amet, consectetur adipiscing elit, sed do eiusmod tempor incididunt ut labore et dolore magna aliqua. Ut enim ad minim veniam, quis nostrud exercitation ullamco laboris nisi ut aliquip ex ea commodo consequat. Duis aute irure dolor in reprehenderit in voluptate velit esse cillum dolore</p>
<a class="btn" href="#book" style="left:665px;top:2039px;width:191px;height:42px">Book an appointment <svg viewBox="0 0 12 12"><rect x="1" y="2" width="10" height="9" fill="none" stroke="#fff" stroke-width="1.4"/><path d="M1 5h10M4 1v2M8 1v2" stroke="#fff" stroke-width="1.4"/></svg></a>

<!-- PRODUCTS -->
<h2 class="section-title" style="top:2302px">Our Products</h2>
<svg class="abs arrow" style="left:45px" width="20" height="30" viewBox="0 0 20 30" aria-hidden="true"><path d="M15 3L5 15l10 12" fill="none" stroke="#222" stroke-width="3"/></svg>
<svg class="abs arrow" style="left:1134px" width="20" height="30" viewBox="0 0 20 30" aria-hidden="true"><path d="M5 3l10 12L5 27" fill="none" stroke="#222" stroke-width="3"/></svg>
<div class="abs card" style="left:112px"><div class="ph" role="img" aria-label="Product photo of a rose quartz face roller"></div><h4>Product Title</h4><p>Lorem ipsum dolor sit amet, cons adipiscing elit, sed do eiusmod tempor</p></div>
<div class="abs card" style="left:443px"><div class="ph" role="img" aria-label="Product photo of a cream tube"></div><h4>Product Title</h4><p>Lorem ipsum dolor sit amet, cons adipiscing elit, sed do eiusmod tempor</p></div>
<div class="abs card" style="left:773px"><div class="ph" role="img" aria-label="Product photo of a roller and serum bottle"></div><h4>Product Title</h4><p>Lorem ipsum dolor sit amet, cons adipiscing elit, sed do eiusmod tempor</p></div>

<!-- STORIES + FOOTER BACKGROUND -->
<svg class="abs" style="left:0;top:2820px" width="1200" height="1145" viewBox="0 0 1200 1145" aria-hidden="true">
  <defs><linearGradient id="footEdge" x1="0" x2="1"><stop offset="0" stop-color="#e8336e"/><stop offset="1" stop-color="#e8336e"/></linearGradient></defs>
  <path d="M0 85Q500 -40 1200 20V700H0Z" fill="#fdf1e8"/>
  <path d="M0 85Q250 20 540 2L500 20Q230 45 0 112Z" fill="#f7891f"/>
  <path d="M0 700Q500 830 1200 700V1145H0Z" fill="#1f1e21"/>
  <path d="M0 700Q500 830 1200 700V668Q700 800 0 700Z" fill="url(#footEdge)"/>
</svg>
<h2 class="section-title" style="top:2930px">Our Stories</h2>
<article class="abs story" style="left:112px">
  <p>Lorem ipsum dolor sit amet, consectetur adipiscing elit, sed do eiusmod tempor incididunt ut labore et dolore magna aliqua. Ut enim ad minim veniam, quis nostrud exercitation ullamco laboris nisi ut aliquip ex ea</p>
  <div class="who"><b>John Doe</b> , &nbsp;Businessman</div><div class="q">”</div>
  <div class="lbl" style="left:113px">Before</div><div class="lbl" style="left:291px">After</div>
  <div class="face" role="img" aria-label="Before photo of a woman's profile" style="left:68px"></div>
  <div class="face" role="img" aria-label="After photo of a woman's profile" style="left:245px"></div>
</article>
<article class="abs story" style="left:617px">
  <p>Lorem ipsum dolor sit amet, consectetur adipiscing elit, sed do eiusmod tempor incididunt ut labore et dolore magna aliqua. Ut enim ad minim veniam, quis nostrud exercitation ullamco laboris nisi ut aliquip ex ea</p>
  <div class="who"><b>John Doe</b> , &nbsp;Businessman</div><div class="q">”</div>
  <div class="lbl" style="left:87px">Before</div><div class="lbl" style="left:315px">After</div>
  <div class="face" role="img" aria-label="Before photo of a man's profile" style="left:68px;background:linear-gradient(180deg,#d9d6d4,#c9a99a)"></div>
  <div class="face" role="img" aria-label="After photo of a man's profile" style="left:265px;background:linear-gradient(180deg,#d9d6d4,#c9a99a)"></div>
</article>

<!-- FOOTER -->
<footer>
  <div class="abs" style="left:150px;top:3690px;width:62px;height:62px;border-radius:50%;border:2px solid var(--pink)"></div>
  <div class="abs" style="left:112px;top:3790px;width:260px;font:700 38px var(--sans);color:var(--pink)">Glow Muse</div>
  <div class="abs" style="left:112px;top:3854px;width:260px;font:400 10px var(--sans);letter-spacing:5px;color:var(--orange)">CONCIERGE AESTHETICS</div>

  <h5 class="abs foot-h" style="left:413px;top:3690px">Quick Links</h5>
  <ul class="abs foot-list" style="left:413px;top:3740px">
    <li>Home</li><li>About Us</li><li>Our Products</li><li>Gallery</li><li>Contact Us</li>
  </ul>

  <h5 class="abs foot-h" style="left:586px;top:3690px">Contact Us</h5>
  <ul class="abs contact" style="left:586px;top:3744px;list-style:none;width:210px">
    <li><span class="ic"></span>+1 555 014 2290</li>
    <li><span class="ic"></span>hello@glowmuse.com</li>
    <li><span class="ic"></span>12 Harbor Lane, Westfield Australia</li>
    <li><span class="ic"></span><u>View Other Location</u></li>
  </ul>

  <h5 class="abs foot-h" style="left:824px;top:3690px">Subscribe Now</h5>
  <p class="abs" style="left:824px;top:3744px;width:260px;font:400 13px/20px var(--sans);color:#fff">Sed ut perspiciatis unde omnis iste natus error sit voluptatem accusantium</p>
  <div class="abs" style="left:824px;top:3806px;width:254px;height:45px;background:#fff;border-radius:23px;display:flex;align-items:center;padding-left:24px;gap:14px;font:400 12px var(--sans);color:#555">
    <svg width="12" height="10" viewBox="0 0 12 10"><rect width="12" height="10" fill="#555"/><path d="M0 0l6 5 6-5" fill="none" stroke="#fff"/></svg>Email Address
  </div>
  <span class="abs" style="left:1033px;top:3806px;width:45px;height:45px;border-radius:50%;background:linear-gradient(135deg,var(--pink),var(--orange));display:flex;align-items:center;justify-content:center"><svg width="16" height="16" viewBox="0 0 16 16"><path d="M1 8l14-6-5 13-2-5z" fill="#fff"/></svg></span>
  <div class="abs socials"><span></span><span></span><span></span><span></span></div>
  <div class="abs copy">© 2022 Glow Muse. All Rights Reserved</div>
</footer>

</body>
</html>
```